Bed Company needs business card

Hello, we are a bed company that makes specialized magnets for beds. We are an alternative healing company. I need a modern and upscale business card. Please incorporate my logo for the card.

Accepted file formats are AI, EPS, and Press-Ready PDFS.

Please include all fonts or convert them to outlines regardless of file type.

If you are designing the card in Photoshop the file Must be 1200dpi.

I am open to anything for the business card.  I really like all of your designs and if you want to change the color of the logo, you can.  I will be making the final selection by Friday.  Thank You for all of your designs.  Feel Free to submit different color logos if you want.  

Reason: I will make a decision Final on Friday April 20th. 2012. Good Luck and Thank you all for the designs.

Target Market(s)

My target Market is people, who are looking for alternative healing.

Industry/Entity Type

Business

Requirements
Must have
• My logo must be incorporated. The front card must have

Name
Job Title

Address
Work
Cell
Fax
email
web

Just put in fake info for the card.

The back of the card. I want the logo on the back with color. I just want it to look modern and cool.

```html
<!DOCTYPE html>
<html lang="en">
<head>
<meta charset="utf-8">
<title>Calmfield Beds – Business Card</title>
<link href="https://fonts.googleapis.com/css2?family=Open+Sans:wght@400;600;700&display=swap" rel="stylesheet">
<style>
  :root {
    --canvas-bg: #e8e6e3;
    --card-green: #5cbc4c;
    --card-green-light: #72c963;
    --band-green: #13682f;
    --band-green-light: #1f7d3c;
    --brand-green: #3a9f34;
    --deep-green: #14602a;
    --web-green: #17652d;
    --white: #ffffff;
    --shadow: rgba(0, 0, 0, 0.18);
  }
  * { box-sizing: border-box; margin: 0; padding: 0; }
  html, body {
    width: 1200px;
    height: 900px;
    overflow: hidden;
    background: var(--canvas-bg);
    font-family: "Open Sans", Arial, sans-serif;
  }
  .canvas {
    position: relative;
    width: 1200px;
    height: 900px;
  }
  .card {
    position: absolute;
    width: 600px;
    height: 343px;
    box-shadow: 0 6px 18px var(--shadow);
    overflow: hidden;
  }

  /* Front */
  .card-front {
    left: 60px;
    top: 100px;
    background: radial-gradient(ellipse at 55% 60%, var(--card-green-light) 0%, var(--card-green) 65%);
    color: var(--white);
  }
  .rule {
    position: absolute;
    left: 0;
    width: 100%;
    height: 3px;
    background: var(--white);
  }
  .rule-top { top: 52px; }
  .rule-bottom { top: 150px; }
  .name-band {
    position: absolute;
    left: 0;
    top: 62px;
    width: 100%;
    height: 80px;
    background: radial-gradient(ellipse at 45% 40%, var(--band-green-light) 0%, var(--band-green) 70%);
    text-align: center;
    padding-top: 10px;
  }
  .person-name {
    font-size: 31px;
    font-weight: 400;
    line-height: 1.15;
  }
  .person-title {
    font-size: 16px;
    font-weight: 400;
  }
  .event-line {
    position: absolute;
    left: 62px;
    top: 184px;
    font-size: 13.5px;
  }
  .contact-list {
    position: absolute;
    left: 68px;
    top: 218px;
    font-size: 13.5px;
    line-height: 19px;
  }
  .contact-row { display: flex; }
  .contact-label { width: 36px; }
  .contact-sep { width: 22px; }
  .online {
    position: absolute;
    left: 68px;
    top: 290px;
    font-size: 13.5px;
    line-height: 19px;
  }
  .online .web { color: var(--web-green); }

  /* Back */
  .card-back {
    left: 540px;
    top: 480px;
    background: var(--white);
  }
  .wordmark {
    position: absolute;
    left: 100px;
    top: 118px;
    display: flex;
    align-items: center;
    gap: 18px;
  }
  .wordmark-square {
    width: 62px;
    height: 62px;
    background: var(--deep-green);
  }
  .wordmark-name {
    font-size: 48px;
    font-weight: 700;
    color: var(--brand-green);
    line-height: 1;
    white-space: nowrap;
  }
  .tagline {
    position: absolute;
    right: 94px;
    top: 196px;
    font-size: 18px;
    letter-spacing: 1.5px;
    color: var(--brand-green);
  }
</style>
</head>
<body>
<main class="canvas">

  <section class="card card-front" aria-label="Business card front">
    <div class="rule rule-top"></div>
    <div class="name-band">
      <h1 class="person-name">Daniel Whitmore</h1>
      <p class="person-title">director</p>
    </div>
    <div class="rule rule-bottom"></div>

    <p class="event-line">May 14-17, 2012, Lakeshore Hall East, Denver CO, Booth 2210</p>

    <div class="contact-list">
      <div class="contact-row"><span class="contact-label">tel</span><span class="contact-sep">:</span><span>(555) 210 4417</span></div>
      <div class="contact-row"><span class="contact-label">cell</span><span class="contact-sep">:</span><span>(555) 318 2096</span></div>
      <div class="contact-row"><span class="contact-label">fax</span><span class="contact-sep">:</span><span>(555) 210 4490</span></div>
    </div>

    <div class="online">
      <p class="email">office@calmfieldbeds.com</p>
      <p class="web">www.calmfield-beds.com</p>
    </div>
  </section>

  <section class="card card-back" aria-label="Business card back">
    <div class="wordmark">
      <span class="wordmark-square"></span>
      <span class="wordmark-name">Calmfield Beds</span>
    </div>
    <p class="tagline">Alternative Healing</p>
  </section>

</main>
</body>
</html>
```